new service company in the field of construction seeks to make the Creation of a PPT

We need a PPT format with a cover page a frame for presentation. our company is based in Paris which was named VORENTIX. we just did our logo attached. Our company offers services to manage and control documents that pass on projects in construction (building, infrastructure, energy, oil and gas etc. ..). We use internet systems to help us, design must show insurance, quality, and safety. Customers should build any type of works and can not build without the approved documents. These documents go through multiple validations, and vorentix staff seconded on projects, coordinate these processes and documents, quality documents, to ensure that project deadlines are met and project management sees his project developed within the period, through regular reporting. the services offered by our company help ensure the project of building on time, to ensure the project manager visibility on what e will not, and can act accordingly.

Target Market(s)

general contractor of engineering construction or big business masters lumber wholesale real estate investor, project ownership in the construction sector

Industry/Entity Type

Construction

Contact Information for Business Card

carte rectangulaire petite taille (4X6cm env)
horizontale ou verticale
prendre en compte les éléments suivants :
logo
nom de société
adresse postale (4 lignes)
teléphone:
mail
role (ex : directeur)
in the back : La qualité documentaire de vos projets

Font styles to use
Sans Serif

Colors
34a7d7
85cae6
cee9f5
0592cd

Requirements
Must have
• The project should have 2 sliders: slider 1. Cover Page 2. slider for the content of presentations THE GOAL IS TO HAVE A VISUAL IDENTITY ON PPT, MY BUSINESS CARDS AND LETTERS must stay in mind and colors of the logo that joined the design must be clean and recall the seriousness, ease. the design must take into account the page numbers Tag line: the documentary quality of your projects information such as tagline and writes must be modifiable
Nice to have
• would require the presentation of the figure shows concepts or reporting table THE GOAL IS TO HAVE A VISUAL IDENTITY ON PPT, MY BUSINESS CARDS AND LETTERS
Should not have
• not to building or building in the logo

```html
<!DOCTYPE html>
<html lang="en">
<head>
<meta charset="utf-8">
<title>VORENTIX – Presentation Identity</title>
<link rel="stylesheet" href="https://fonts.googleapis.com/css2?family=Cabin:wght@400;500&display=swap">
<style>
  :root {
    --brand-blue: #2160a8;
    --brand-blue-light: #6f9bd0;
    --brand-blue-back: #2872ae;
    --backdrop: #d3dadd;
    --paper: #ffffff;
    --ink: #1e1e1e;
    --ink-soft: #7a7a7a;
    --rule: #9fb8d8;
  }
  * { box-sizing: border-box; margin: 0; padding: 0; }
  html, body { width: 1200px; height: 1200px; overflow: hidden; }
  body {
    background: var(--backdrop);
    font-family: "Cabin", "Gill Sans", sans-serif;
    position: relative;
  }
  .slide {
    position: absolute;
    width: 578px;
    height: 326px;
    background: var(--paper);
    overflow: hidden;
    box-shadow: 2px 3px 6px rgba(0,0,0,0.25);
  }
  .slide--cover-plain { left: 22px; top: 26px; }
  .slide--cover-photo { left: 613px; top: 26px; }
  .slide--content-a  { left: 22px; top: 450px; }
  .slide--content-b  { left: 613px; top: 450px; }
  .slide--closing    { left: 312px; top: 850px; background: var(--brand-blue-back); }

  /* Cover */
  .cover-photo {
    position: absolute; left: 0; top: 0; width: 100%; height: 210px;
    background: linear-gradient(120deg, #b7c3cc 0%, #dde3e8 45%, #a9b6c1 100%);
  }
  .cover-band {
    position: absolute; left: 0; top: 208px; width: 100%; height: 118px;
    background: var(--brand-blue);
  }
  .cover-shape { position: absolute; left: 0; top: 0; }
  .cover-name {
    position: absolute; left: 167px; top: 170px;
    font-size: 29px; font-weight: 500; letter-spacing: 0.5px;
    color: var(--brand-blue);
  }
  .cover-title {
    position: absolute; left: 34px; top: 255px;
    font-size: 19px; color: var(--paper); letter-spacing: 0.2px;
  }
  .cover-date {
    position: absolute; left: 34px; top: 280px;
    font-size: 10px; color: #c9d8ec;
  }
  .cover-rule {
    position: absolute; left: 34px; top: 299px;
    width: 248px; height: 1px; background: var(--rule);
  }

  /* Content */
  .bar-top { position: absolute; left: 0; top: 0; width: 100%; height: 10px; background: var(--brand-blue); }
  .bar-bottom { position: absolute; left: 0; bottom: 0; width: 100%; height: 8px; background: var(--brand-blue); }
  .content-title {
    position: absolute; left: 32px; top: 22px;
    font-size: 16px; color: var(--ink);
  }
  .content-subtitle {
    position: absolute; left: 32px; top: 42px;
    font-size: 10px; color: var(--brand-blue);
  }
  .slide--content-b .content-title { left: 37px; top: 22px; color: var(--brand-blue); }
  .slide--content-b .content-subtitle { left: 37px; top: 42px; color: var(--ink-soft); }
  .dots { position: absolute; left: 37px; top: 57px; display: flex; gap: 3px; }
  .dots span { width: 3px; height: 3px; border-radius: 50%; background: var(--brand-blue); }

  .mark-dot { position: absolute; border-radius: 50%; background: var(--brand-blue); }

  .feature { position: absolute; width: 170px; text-align: center; }
  .feature__photo {
    width: 122px; height: 122px; border-radius: 50%; margin: 0 auto;
    background: radial-gradient(circle at 40% 40%, #8aa6c4 0%, #3a5b85 50%, #1b2a40 100%);
  }
  .feature__photo--gears { background: radial-gradient(circle at 50% 45%, #b5b1a3 0%, #6b6a62 45%, #2d2c2a 100%); }
  .feature__photo--board { background: radial-gradient(circle at 60% 35%, #e5eef0 0%, #7e9aa1 40%, #2b3b40 100%); }
  .feature__caption { margin-top: 12px; font-size: 10.5px; color: var(--ink); }
  .feature__text { margin-top: 4px; font-size: 6.6px; line-height: 1.3; color: var(--ink); padding: 0 6px; }

  .footer-name {
    position: absolute; left: 35px; bottom: 18px;
    font-size: 10px; font-weight: 500; color: var(--brand-blue); letter-spacing: 0.3px;
  }
  .page-num {
    position: absolute; width: 14px; height: 14px; border-radius: 50%;
    font-size: 6px; display: flex; align-items: center; justify-content: center;
  }
  .page-num--light { right: 34px; bottom: 10px; background: var(--paper); color: var(--ink-soft); border: 1px solid #ddd; }
  .page-num--solid { right: 34px; bottom: 14px; background: var(--brand-blue); color: var(--paper); }

  /* Closing */
  .closing-name {
    position: absolute; left: 0; top: 28px; width: 100%; text-align: center;
    font-size: 50px; font-weight: 500; color: var(--paper); letter-spacing: 1px;
  }
  .closing-dot {
    position: absolute; left: 233px; top: 89px; width: 112px; height: 112px;
    border-radius: 50%; background: var(--paper);
  }
  .closing-tagline {
    position: absolute; left: 0; top: 253px; width: 100%; text-align: center;
    font-size: 18px; color: var(--paper);
  }
</style>
</head>
<body>

<section class="slide slide--cover-plain">
  <div class="cover-band"></div>
  <svg class="cover-shape" width="578" height="326" viewBox="0 0 578 326">
    <circle cx="422" cy="128" r="132" fill="#ffffff"/>
    <circle cx="422" cy="128" r="108" fill="var(--brand-blue)"/>
  </svg>
  <div class="cover-name">VORENTIX</div>
  <div class="cover-title">LOREM IPSUM DOLOR SIT AMET</div>
  <div class="cover-date">Date</div>
  <div class="cover-rule"></div>
</section>

<section class="slide slide--cover-photo">
  <div class="cover-photo" role="img" aria-label="Muted blue-grey photo of a businessman's hands holding a stack of documents"></div>
  <div class="cover-band"></div>
  <svg class="cover-shape" width="578" height="326" viewBox="0 0 578 326">
    <circle cx="422" cy="128" r="132" fill="#b4c2cf" opacity="0.85"/>
    <circle cx="422" cy="128" r="108" fill="var(--brand-blue)"/>
  </svg>
  <div class="cover-name">VORENTIX</div>
  <div class="cover-title">LOREM IPSUM DOLOR SIT AMET</div>
  <div class="cover-date">Date</div>
  <div class="cover-rule"></div>
</section>

<section class="slide slide--content-a">
  <div class="bar-top"></div>
  <div class="content-title">LOREM IPSUM DOLOR SIT AMET</div>
  <div class="content-subtitle">Lorem ipsum dolor sit amet</div>
  <div class="mark-dot" style="left:506px; top:12px; width:37px; height:37px;"></div>

  <div class="feature" style="left:44px; top:83px;">
    <div class="feature__photo" role="img" aria-label="Photo of a robotic gripper tool in blue light"></div>
    <div class="feature__caption">Lorem ipsum</div>
    <div class="feature__text">Lorem ipsum dolor sit amet, consetetur sadipscing elitr, sed diam nonumy eirmod tempor invidunt ut labore et dolore magna aliquyam erat, sed diam voluptua. At vero eos et accusam et justo duo dolores et ea rebum.</div>
  </div>
  <div class="feature" style="left:204px; top:83px;">
    <div class="feature__photo feature__photo--gears" role="img" aria-label="Photo of industrial gears and machinery"></div>
    <div class="feature__caption">Lorem ipsum</div>
    <div class="feature__text">Lorem ipsum dolor sit amet, consetetur sadipscing elitr, sed diam nonumy eirmod tempor invidunt ut labore et dolore magna aliquyam erat, sed diam voluptua. At vero eos et accusam et justo duo dolores et ea rebum.</div>
  </div>
  <div class="feature" style="left:365px; top:83px;">
    <div class="feature__photo feature__photo--board" role="img" aria-label="Photo of an electronic circuit board"></div>
    <div class="feature__caption">Lorem ipsum</div>
    <div class="feature__text">Lorem ipsum dolor sit amet, consetetur sadipscing elitr, sed diam nonumy eirmod tempor invidunt ut labore et dolore magna aliquyam erat, sed diam voluptua. At vero eos et accusam et justo duo dolores et ea rebum.</div>
  </div>

  <div class="footer-name">VORENTIX</div>
  <div class="page-num page-num--light">32</div>
  <div class="bar-bottom"></div>
</section>

<section class="slide slide--content-b">
  <div class="content-title">LOREM IPSUM DOLOR SIT AMET</div>
  <div class="content-subtitle">Lorem ipsum dolor sit amet</div>
  <div class="dots"><span></span><span></span><span></span></div>
  <div class="mark-dot" style="left:507px; top:20px; width:42px; height:42px;"></div>

  <div class="feature" style="left:43px; top:91px;">
    <div class="feature__photo" role="img" aria-label="Photo of a robotic gripper tool in blue light"></div>
    <div class="feature__caption">Lorem ipsum</div>
    <div class="feature__text">Lorem ipsum dolor sit amet, consetetur sadipscing elitr, sed diam nonumy eirmod tempor invidunt ut labore et dolore magna aliquyam erat, sed diam voluptua. At vero eos et accusam et justo duo dolores et ea rebum.</div>
  </div>
  <div class="feature" style="left:204px; top:91px;">
    <div class="feature__photo feature__photo--gears" role="img" aria-label="Photo of industrial gears and machinery"></div>
    <div class="feature__caption">Lorem ipsum</div>
    <div class="feature__text">Lorem ipsum dolor sit amet, consetetur sadipscing elitr, sed diam nonumy eirmod tempor invidunt ut labore et dolore magna aliquyam erat, sed diam voluptua. At vero eos et accusam et justo duo dolores et ea rebum.</div>
  </div>
  <div class="feature" style="left:365px; top:91px;">
    <div class="feature__photo feature__photo--board" role="img" aria-label="Photo of an electronic circuit board"></div>
    <div class="feature__caption">Lorem ipsum</div>
    <div class="feature__text">Lorem ipsum dolor sit amet, consetetur sadipscing elitr, sed diam nonumy eirmod tempor invidunt ut labore et dolore magna aliquyam erat, sed diam voluptua. At vero eos et accusam et justo duo dolores et ea rebum.</div>
  </div>

  <div class="footer-name" style="left:37px; bottom:14px; font-size:12px;">VORENTIX</div>
  <div class="page-num page-num--solid">14</div>
</section>

<section class="slide slide--closing">
  <div class="closing-name">VORENTIX</div>
  <div class="closing-dot"></div>
  <div class="closing-tagline">Lorem ipsum dolor</div>
</section>

</body>
</html>
```